Copper lark buildworks

Copper lark buildworks is a small construction company.
Who is a licenced builder, Carpenter, joiner,
working on heritage ,new build, speacial projects and sometimes furniture

Industry/Entity Type

Construction

```html
<!DOCTYPE html>
<html lang="en">
<head>
<meta charset="utf-8">
<title>Copper lark buildworks – business card</title>
<link rel="stylesheet" href="https://fonts.googleapis.com/css2?family=Montserrat:wght@400;500;600;700;800&display=swap">
<style>
  :root {
    --brand-green: #2f8a12;
    --band-black: #0d0d0d;
    --card-white: #f7f7f5;
    --ink: #1c1c1c;
    --backdrop: #e4e4e1;
  }
  html, body {
    margin: 0;
    width: 1200px;
    height: 1000px;
    overflow: hidden;
    background: var(--backdrop);
  }
  .canvas {
    position: relative;
    width: 1200px;
    height: 1000px;
  }
  .business-card {
    position: absolute;
    left: 150px;
    top: 243px;
    width: 900px;
    height: 514px;
    filter: drop-shadow(0 8px 18px rgba(0,0,0,0.18));
  }
  .business-card text {
    font-family: "Montserrat", sans-serif;
  }
  .brand-name { fill: var(--brand-green); font-weight: 800; font-size: 36px; }
  .holder-name { fill: #ffffff; font-weight: 700; font-size: 21px; }
  .holder-role { fill: var(--ink); font-weight: 500; font-size: 12.5px; }
  .services-lead { fill: var(--brand-green); font-weight: 500; font-size: 17px; }
  .services-item { fill: var(--ink); font-weight: 600; font-size: 17px; }
  .contact-line { fill: var(--ink); font-weight: 500; font-size: 19px; }
  .address-line { fill: var(--ink); font-weight: 500; font-size: 22px; }
  .icon-disc { fill: var(--brand-green); }
  .icon-glyph { fill: none; stroke: #ffffff; stroke-width: 1.8; stroke-linecap: round; stroke-linejoin: round; }
</style>
</head>
<body>
<main class="canvas">
  <svg class="business-card" viewBox="0 0 900 514" xmlns="http://www.w3.org/2000/svg" aria-label="Copper lark buildworks business card">
    <defs>
      <clipPath id="card-shape">
        <rect x="0" y="0" width="900" height="514" rx="32" ry="32"/>
      </clipPath>
    </defs>

    <g clip-path="url(#card-shape)">
      <rect class="card-face" x="0" y="0" width="900" height="514" fill="var(--card-white)"/>

      <g class="brand-strip" transform="translate(0,360) rotate(-9.5)">
        <text class="brand-name" x="48" y="-50">COPPER LARK</text>
        <text class="brand-name" x="48" y="-12">BUILDWORKS</text>

        <polygon class="name-band" points="-40,0 472,0 456,44 -40,44" fill="var(--brand-green)"/>
        <text class="holder-name" x="444" y="21" text-anchor="end">Rowan Tate</text>
        <text class="holder-role" x="438" y="38" text-anchor="end">Licenced Builder &amp; Carpenter</text>

        <rect class="black-band" x="-60" y="50" width="1100" height="40" fill="var(--band-black)"/>
        <polygon class="corner-tab" points="868,44 884,12 1000,12 1000,44" fill="var(--brand-green)"/>
      </g>

      <g class="services">
        <text class="services-lead" x="600" y="60">working on</text>
        <text class="services-item" x="614" y="82">heritage</text>
        <text class="services-item" x="628" y="104">new build</text>
        <text class="services-item" x="642" y="126">speacial projects</text>
        <text class="services-item" x="656" y="148">and furniture</text>
      </g>

      <g class="contacts">
        <g class="contact-phone">
          <circle class="icon-disc" cx="611" cy="373" r="10"/>
          <path class="icon-glyph" d="M606.5 368.5 q0 -2 2 -2 l1.5 0 l1 2.5 l-1.5 1 q1 2.5 3.5 3.5 l1 -1.5 l2.5 1 l0 1.5 q0 2 -2 2 q-8 -1 -8 -8z"/>
          <text class="contact-line" x="630" y="380">0491203576</text>
        </g>
        <g class="contact-email">
          <circle class="icon-disc" cx="623" cy="403" r="10"/>
          <rect class="icon-glyph" x="617" y="398.5" width="12" height="9" rx="1"/>
          <path class="icon-glyph" d="M617 398.5 l6 5 l6 -5"/>
          <text class="contact-line" x="642" y="410">rowan@copperlark.com</text>
        </g>
        <g class="contact-web">
          <circle class="icon-disc" cx="635" cy="433" r="10"/>
          <circle class="icon-glyph" cx="635" cy="433" r="6"/>
          <path class="icon-glyph" d="M629 433 h12 M635 427 q-3.5 6 0 12 M635 427 q3.5 6 0 12"/>
          <text class="contact-line" x="654" y="440">www.copperlark.com</text>
        </g>
      </g>

      <g class="address">
        <text class="address-line" x="96" y="468">Your Street Address Here</text>
        <text class="address-line" x="112" y="497">Singapore 56789</text>
      </g>
    </g>
  </svg>
</main>
</body>
</html>
```